Small environmental consultancy needs a simple but professional web design

We are a boutique environmental consultancyand contracting business located in Margaret River in the South West of Western Australia.

We have two arms
1) Consulting which offers environmental planning, management and assessment services primarily to local government and the development industry.
2) Contracting which implements on site plans and on ground works primarily involving revegetation, bush regeneration and environmental weed control.

We need a simple yet professional web design within the wordpress platform that commmunicates professionalism, experience and technical expertise without appearing too corporate.

Something like this structure appeals:
http://fernquill.net.au/environment-services/
or
http://www.tallowbrookenvironmental.com.au/index.php

(without the image gallery function)

Target Market(s)

Local Government Officers deciding on tenders;
Developers, Engineers, Town Planning consultants looking for environmental expertise

Industry/Entity Type

Business

Number of Pages Required

5+ page

Font styles to use
Sans Serif

Colors
33a6d7
9bcb3c

Requirements
Must have
• Pages required include:
• Home
• Environmental Planning and Management
• Revegetation and Regeneration Implementation (This page can mirror the Environmental Planning and Management page exactly in structure but with different text and images)
• About Us (I think that this page can be relatively simple and generic)
• Contact (I think that this page can be very simple and generic)
Nice to have
• An ability to start out basic and quicikly establish a website presence and then build in additional drop downs and pages over time.
Should not have
• It does not need a photo gallery page;
• It does not need a major amount of space dedicated to social media and blogs etc as this is not currently particularly active area for us

```html
<!DOCTYPE html>
<html lang="en">
<head>
<meta charset="utf-8">
<title>Quenda Ecoservices</title>
<link href="https://fonts.googleapis.com/css2?family=Exo+2:wght@400;500;600;700&family=Open+Sans:wght@400;600;700&display=swap" rel="stylesheet">
<style>
:root{
  --green:#8cc021;
  --green-dark:#5e8a12;
  --blue:#33a6d7;
  --text:#3a3a3a;
  --muted:#5f5f5f;
  --band:#edece6;
  --footer:#ebebeb;
  --white:#ffffff;
  --line:#d8d8d8;
}
*{box-sizing:border-box;margin:0;padding:0}
html,body{width:689px;height:1200px;overflow:hidden;background:var(--white)}
body{position:relative;font-family:"Open Sans",sans-serif;color:var(--text)}
a{color:inherit;text-decoration:none}

/* header */
.site-header{position:absolute;left:0;top:0;width:689px;height:68px;background:var(--white)}
.brand{position:absolute;left:57px;top:22px;display:flex;align-items:center;gap:6px;font-family:"Exo 2",sans-serif;font-weight:600;font-size:13px;color:var(--green-dark)}
.brand-dot{width:14px;height:14px;border-radius:50%;background:var(--green)}
.call-top{position:absolute;left:419px;top:15px;font-family:"Exo 2",sans-serif;font-size:7.4px;font-weight:500;white-space:nowrap}
.search{position:absolute;left:526px;top:13px;width:106px;height:15px;border-radius:8px;background:#e9e9e9;font-size:7px;color:#888;padding:3px 0 0 8px}
.search-btn{position:absolute;right:1px;top:1px;width:13px;height:13px;border-radius:50%;background:var(--green-dark)}
.main-nav{position:absolute;left:0;top:46px;width:689px;height:14px;font-family:"Exo 2",sans-serif;font-size:7.6px;font-weight:500;white-space:nowrap}
.main-nav > *{position:absolute;top:1px}
.main-nav svg{top:0}

/* hero */
.hero{position:absolute;left:0;top:68px;width:689px;height:364px;background:linear-gradient(180deg,#6f9a2a 0%,#3f6b18 45%,#4f7a22 70%,#5b5a8a 88%,#3c5a22 100%)}
.hero-title{position:absolute;top:201px;width:100%;text-align:center;font-family:"Exo 2",sans-serif;font-weight:700;font-size:26.5px;color:var(--white);letter-spacing:-.3px;white-space:nowrap}
.hero-sub{position:absolute;top:229px;width:100%;text-align:center;font-family:"Exo 2",sans-serif;font-weight:500;font-size:17px;color:var(--white)}
.hero-dots{position:absolute;left:305px;top:336px;width:79px;height:22px;border-radius:11px;background:var(--green);display:flex;align-items:center;justify-content:center;gap:4px}
.hero-dots span{width:9px;height:9px;border-radius:50%;border:1.5px solid var(--white)}
.hero-dots span.on{background:var(--white)}

/* welcome */
.welcome h1{position:absolute;top:457px;width:100%;text-align:center;font-family:"Exo 2",sans-serif;font-weight:400;font-size:17px;color:var(--text)}
.welcome h1 b{color:var(--green);font-weight:500}
.welcome p{position:absolute;left:60px;top:487px;width:569px;text-align:center;font-size:7.5px;line-height:13px;color:var(--muted)}

/* cards */
.features{position:absolute;left:0;top:565px;width:689px;height:224px;background:var(--band)}
.card{position:absolute;top:16px;width:132px;height:192px;background:var(--white);padding:1px}
.card-img{height:95px}
.card h3{font-family:"Open Sans",sans-serif;font-size:7.5px;font-weight:700;text-transform:uppercase;margin:8px 0 0 6px;letter-spacing:0}
.card p{font-size:7.6px;line-height:13px;color:var(--muted);margin:5px 6px 0 6px}
.card .more{display:block;font-size:6.5px;color:var(--blue);margin:5px 0 0 6px}

/* testimonials */
.clients h2{position:absolute;top:804px;width:100%;text-align:center;font-family:"Exo 2",sans-serif;font-weight:400;font-size:17px}
.clients h2 b{font-weight:600}
.rule{position:absolute;left:334px;top:835px;width:21px;height:2px;background:var(--blue)}
.quote{position:absolute;top:868px;width:140px}
.quote .mark{position:absolute;left:0;top:-6px;font-family:"Exo 2",sans-serif;font-weight:700;font-size:34px;color:var(--green);line-height:1}
.quote p{margin-left:22px;font-size:7.5px;line-height:11.5px;color:var(--muted)}
.quote .name{margin:5px 0 0 22px;font-family:"Exo 2",sans-serif;font-weight:600;font-size:7.5px}
.avatar{position:absolute;top:68px;left:14px;width:68px;height:68px;border-radius:50%;border:2px solid #dcdcdc;background:radial-gradient(circle at 50% 45%,#c9b3a0,#8a8a8a)}
.arrow{position:absolute;top:921px}

/* footer */
.site-footer{position:absolute;left:0;top:1024px;width:689px;height:176px;background:var(--footer)}
.site-footer h4{font-family:"Exo 2",sans-serif;font-weight:600;font-size:10px;text-transform:uppercase}
.site-footer h4 span{font-weight:400}
.links{list-style:none;font-size:6.6px;line-height:11px;margin-top:5px}
.col-about{position:absolute;left:57px;top:17px}
.col-legal{position:absolute;left:231px;top:17px}
.call-now{position:absolute;left:57px;top:84px}
.phone{position:absolute;left:57px;top:103px;display:flex;align-items:center;gap:5px;font-family:"Exo 2",sans-serif;font-size:12.5px;color:var(--green)}
.contact{position:absolute;left:352px;top:20px;width:270px}
.field{position:absolute;height:19px;background:var(--white);border:1px solid var(--line);font-size:8px;color:#9a9a9a;padding:3px 7px}
.send{position:absolute;left:0;top:89px;width:83px;height:23px;background:linear-gradient(#8fbd2a,#6f9a18);color:var(--white);font-family:"Exo 2",sans-serif;font-size:9px;font-weight:500;text-align:center;padding-top:5px}
.footer-rule{position:absolute;left:57px;top:148px;width:575px;height:1px;background:#dcdcdc}
.copyright{position:absolute;left:57px;top:157px;font-size:6.6px}
</style>
</head>
<body>

<header class="site-header">
  <a class="brand" href="#"><span class="brand-dot"></span>Quenda Ecoservices</a>
  <div class="call-top">CALL US NOW: 8888 888 888</div>
  <div class="search">Search<span class="search-btn"></span></div>
  <nav class="main-nav">
    <svg style="left:179px" width="13" height="12" viewBox="0 0 13 12"><path d="M6.5 0 0 6h2v6h3.5V8h2v4H11V6h2z" fill="#111"/></svg>
    <a style="left:198px" href="#">ENVIRONMENTAL PLANNING AND MANAGEMENT</a>
    <a style="left:382px" href="#">REVEGETATION AND BUSH REGENERATION</a>
    <a style="left:546px" href="#">ABOUT US</a>
    <a style="left:594px" href="#">CONTACTS</a>
  </nav>
</header>

<section class="hero" role="img" aria-label="Sunlit woodland path among tall trees with bluebells">
  <div class="hero-title">LOREM IPSUM DOLOR SIT AMET</div>
  <div class="hero-sub">CONSECTETUR ADIPISCING ELIT</div>
  <div class="hero-dots"><span class="on"></span><span></span><span></span><span></span><span></span></div>
</section>

<section class="welcome">
  <h1>WELCOME TO <b>QUENDA ECOSERVICES</b></h1>
  <p>Lorem ipsum dolor sit amet, consectetur adipiscing elit, sed do eiusmod tempor incididunt ut labore et dolore magna aliqua. Ut enim ad minim veniam, quis nostrud exercitation ullamco laboris nisi ut aliquip ex ea commodo consequat. Duis aute irure dolor in reprehenderit in voluptate velit esse cillum dolore eu fugiat nulla pariatur. Excepteur sint occaecat cupidatat non proident, sunt in culpa qui officia deserunt mollit anim id est laborum. Lorem ipsum dolor sit amet, consectetur adipiscing elit, sed do eiusmod tempor incididunt ut labore et dolore magna aliqua.</p>
</section>

<section class="features">
  <article class="card" style="left:57px">
    <div class="card-img" role="img" aria-label="Handshake in front of green forest" style="background:linear-gradient(135deg,#7fae4a,#2f4a1c 60%,#d9d9d9)"></div>
    <h3>About us</h3>
    <p>Lorem ipsum dolor sit amet, consectetur adipiscing elit, sed do eiusmod tempor incididunt ut labore et dolore.</p>
    <a class="more" href="#">READ MORE ▸</a>
  </article>
  <article class="card" style="left:205px">
    <div class="card-img" role="img" aria-label="Pink thistle flower close-up" style="background:radial-gradient(circle at 50% 35%,#d23fb0,#8fa84a 70%)"></div>
    <h3>Our services</h3>
    <p>Lorem ipsum dolor sit amet, consectetur adipiscing elit, sed do eiusmod tempor incididunt ut labore et dolore.</p>
    <a class="more" href="#">READ MORE ▸</a>
  </article>
  <article class="card" style="left:353px">
    <div class="card-img" role="img" aria-label="Pink and white cosmos flowers" style="background:linear-gradient(135deg,#5f9a3a,#e7b6cf 50%,#4f8a2e)"></div>
    <h3>Current project</h3>
    <p>Lorem ipsum dolor sit amet, consectetur adipiscing elit, sed do eiusmod tempor incididunt ut labore et dolore.</p>
    <a class="more" href="#">READ MORE ▸</a>
  </article>
  <article class="card" style="left:501px">
    <div class="card-img" role="img" aria-label="Purple bellflowers" style="background:linear-gradient(135deg,#6b4fb0,#3d2f7a 50%,#9a9a3a)"></div>
    <h3>Why us?</h3>
    <p>Lorem ipsum dolor sit amet, consectetur adipiscing elit, sed do eiusmod tempor incididunt ut labore et dolore.</p>
    <a class="more" href="#">READ MORE ▸</a>
  </article>
</section>

<section class="clients">
  <h2><b>WHAT</b> OUR CLIENTS THINK</h2>
  <div class="rule"></div>
  <svg class="arrow" style="left:64px" width="12" height="24" viewBox="0 0 12 24"><path d="M11 1 1 12l10 11" fill="none" stroke="#bbb" stroke-width="1.2"/></svg>
  <svg class="arrow" style="left:612px" width="12" height="24" viewBox="0 0 12 24"><path d="M1 1l10 11L1 23" fill="none" stroke="#bbb" stroke-width="1.2"/></svg>
  <blockquote class="quote" style="left:96px">
    <span class="mark">“</span>
    <p>Lorem ipsum dolor sit amet, consectetur adipiscing elit, sed do eiusmod tempor incididunt ut labore et dolore magna aliqua.</p>
    <div class="name">Daniel Marsh</div>
    <div class="avatar" role="img" aria-label="Client portrait"></div>
  </blockquote>
  <blockquote class="quote" style="left:277px">
    <span class="mark">“</span>
    <p>Lorem ipsum dolor sit amet, consectetur adipiscing elit, sed do eiusmod tempor incididunt ut labore et dolore magna aliqua.</p>
    <div class="name">Tom Fenwick</div>
    <div class="avatar" role="img" aria-label="Client portrait"></div>
  </blockquote>
  <blockquote class="quote" style="left:458px">
    <span class="mark">“</span>
    <p>Lorem ipsum dolor sit amet, consectetur adipiscing elit, sed do eiusmod tempor incididunt ut labore et dolore magna aliqua.</p>
    <div class="name">Daniel Marsh</div>
    <div class="avatar" role="img" aria-label="Client portrait"></div>
  </blockquote>
</section>

<footer class="site-footer">
  <div class="col-about">
    <h4>About</h4>
    <ul class="links"><li>Environmental Planning and Management</li><li>Revegetation and Bush Regeneration</li><li>Contacts</li></ul>
  </div>
  <div class="col-legal">
    <h4>Legal</h4>
    <ul class="links"><li>Terms of Service</li><li>Privacy Policy</li><li>Cookie Policy</li></ul>
  </div>
  <h4 class="call-now">Call <span>us now:</span></h4>
  <div class="phone">
    <svg width="11" height="11" viewBox="0 0 24 24"><path d="M6.6 10.8a15 15 0 0 0 6.6 6.6l2.2-2.2c.3-.3.7-.4 1-.2 1.1.4 2.3.6 3.6.6.6 0 1 .4 1 1V20c0 .6-.4 1-1 1A17 17 0 0 1 3 4c0-.6.4-1 1-1h3.5c.6 0 1 .4 1 1 0 1.3.2 2.5.6 3.6.1.3 0 .7-.2 1z" fill="#444"/></svg>
    +8888 888 888
  </div>
  <div class="contact">
    <h4>Contact <span>us</span></h4>
    <div class="field" style="left:0;top:20px;width:132px">Name</div>
    <div class="field" style="left:138px;top:20px;width:132px">E-mail</div>
    <div class="field" style="left:0;top:45px;width:270px;height:38px">Message</div>
    <div class="send">Send Message</div>
  </div>
  <div class="footer-rule"></div>
  <div class="copyright">© 2015, Quenda Ecoservices. All Rights Reserved.</div>
</footer>

</body>
</html>
```